Elegant Tevani Rhum Label Design-

We are creating a Rum Distillery in the paradise island of Bora Bora which is a beautiful and exclusive honeymoon and tourist destination in the South Pacific. Our Rum label needs to reflect the beauty of Bora Bora and French Polynesia.
We would like to see designs that include the image of Mount Otemanu (* the mountain of Bora Bora) with an overwater bungalow in the image with the lagoon. We would like the label to have a turquoise color theme with either silver, white, or gold as the outline of the images. We are also open to some tropical colors as well that represent this paradise. The image needs to represent high quality class. The bottle will be sold mostly to tourist at a premium price.

On the label it needs to have Tevani Rhum as the main name-
Subheader- Light Rhum
Sub Sub header- Distilled and Bottled in Bora Bora
It needs to have 40% vol and 70cl on the label

Target Market(s)

American tourists in Bora Bora, French Polynesia

Industry/Entity Type

Rum Distillery

Colors
0094D4
00A9DD
6FCCEA
C7EBF8
E9F6FB
00AB8E
00BBA5
67D7C9
C6EFE9
E9F9F6

Requirements
Must have
• The mountain image of Otemanu and an overwater bungalow which is symbolic of Bora Bora.

```html
<!DOCTYPE html>
<html lang="en">
<head>
<meta charset="UTF-8">
<title>Tevani Rhum – Light White Rum Label</title>
<link rel="stylesheet" href="https://fonts.googleapis.com/css2?family=Cinzel:wght@500;700;900&family=Great+Vibes&family=Pinyon+Script&display=swap">
<style>
  :root {
    --page: #ffffff;
    --cream: #f1efe4;
    --cream-light: #f7f5ec;
    --ink: #3a3a3c;
    --teal: #1f8f97;
    --teal-deep: #177a82;
    --teal-script: #2a9ba0;
    --slate: #5e6470;
    --gold-dark: #9a7a2c;
    --gold: #c9ad6a;
    --gold-light: #e6d4a0;
    --flag-red: #c8102e;
  }
  * { box-sizing: border-box; margin: 0; padding: 0; }
  html, body {
    width: 1200px; height: 1200px; overflow: hidden;
    background: var(--page);
  }
  .canvas {
    width: 1200px; height: 1200px;
    display: flex; align-items: center; justify-content: center;
  }
  .label {
    width: 720px; height: 1080px;
    background: var(--cream);
    display: flex; flex-direction: column;
    box-shadow: 0 0 0 1px #e4e1d3;
  }
  .label__main {
    flex: 1;
    display: flex; flex-direction: column; align-items: center;
    padding-top: 60px;
  }
  .tagline {
    font-family: "Great Vibes", cursive;
    color: var(--teal-script);
    font-size: 44px;
    transform: rotate(-4deg);
    line-height: 1;
  }
  .scene {
    width: 380px; height: 310px; margin-top: 10px;
    border-radius: 46% 54% 40% 60% / 55% 50% 50% 45%;
    background:
      radial-gradient(ellipse at 50% 35%, #4f8a4c 0 18%, transparent 38%),
      radial-gradient(ellipse at 50% 80%, #4cc6c0 0 25%, transparent 55%),
      radial-gradient(ellipse at 60% 20%, #c9dde9 0 20%, transparent 50%),
      var(--cream);
  }
  .est {
    margin-top: 26px;
    font-family: "Cinzel", serif; font-weight: 700;
    color: var(--ink); font-size: 24px; letter-spacing: 1px;
  }
  .brand {
    font-family: "Pinyon Script", cursive;
    color: var(--ink);
    font-size: 140px; line-height: 1.05;
    margin-top: 6px;
  }
  .spirit {
    font-family: "Cinzel", serif; font-weight: 900;
    color: var(--teal);
    font-size: 80px; letter-spacing: 4px; line-height: 1;
    margin-top: 14px;
  }
  .style {
    font-family: "Cinzel", serif; font-weight: 700;
    color: var(--slate);
    font-size: 29px; letter-spacing: 2px;
    margin-top: 10px;
  }
  .band {
    height: 64px;
    background: linear-gradient(90deg, var(--gold-dark), var(--gold-light) 25%, var(--gold) 60%, var(--gold-dark));
    display: flex; align-items: center; justify-content: center;
    font-family: "Great Vibes", cursive;
    color: #3d3626; font-size: 34px;
  }
  .band__dot { margin: 0 14px; font-family: "Cinzel", serif; font-size: 18px; }
  .label__base {
    height: 300px;
    background: linear-gradient(180deg, var(--teal) 0%, var(--teal-deep) 100%);
    padding: 30px 36px 34px;
  }
  .ticket {
    height: 100%;
    background: var(--cream-light);
    border: 2px dashed var(--gold);
    display: flex; align-items: center;
    padding: 0 30px 0 16px;
  }
  .seal {
    width: 170px; height: 170px; border-radius: 50%;
    background: radial-gradient(circle, #c9a864 0 34%, var(--gold-light) 36% 62%, #d6bd7f 64% 100%);
    flex-shrink: 0;
  }
  .details {
    margin-left: 30px; flex: 1;
    border-left: 1px solid #cfc7ad;
    padding-left: 16px;
    font-family: "Cinzel", serif; font-weight: 700;
    color: var(--ink);
  }
  .origin { display: flex; align-items: center; gap: 14px; margin-bottom: 10px; }
  .flag { width: 54px; height: 34px; flex-shrink: 0; }
  .origin__text { font-size: 11px; line-height: 1.25; }
  .field {
    font-size: 15px; padding: 10px 0 12px;
    border-bottom: 1px dotted #9c9888;
  }
  .specs { font-size: 18px; line-height: 1.2; margin-top: 12px; }
</style>
</head>
<body>
<div class="canvas">
  <article class="label">
    <section class="label__main">
      <p class="tagline">Premium Rhum</p>
      <div class="scene" role="img" aria-label="Watercolour illustration of Mount Otemanu rising over the turquoise lagoon with an overwater bungalow"></div>
      <p class="est">Est. 2025</p>
      <h1 class="brand">Tevani</h1>
      <p class="spirit">RHUM</p>
      <p class="style">A Light White Rhum</p>
    </section>
    <div class="band">Small Batch <span class="band__dot">•</span> Limited Edition</div>
    <section class="label__base">
      <div class="ticket">
        <div class="seal" role="img" aria-label="Gold seal with an outline of the island"></div>
        <div class="details">
          <div class="origin">
            <svg class="flag" viewBox="0 0 54 34" aria-hidden="true">
              <rect width="54" height="34" fill="#fff" stroke="#ddd"/>
              <rect width="54" height="8.5" fill="var(--flag-red)"/>
              <rect y="25.5" width="54" height="8.5" fill="var(--flag-red)"/>
            </svg>
            <p class="origin__text">Distilled &amp; Bottled in:<br>Bora Bora,<br>French Polynesia</p>
          </div>
          <p class="field">Batch No.:</p>
          <p class="field">Bottle No.:</p>
          <p class="specs">40% Alc Vol.<br>70cl</p>
        </div>
      </div>
    </section>
  </article>
</div>
</body>
</html>
```